Northfield Builders Guild Business card

We are looking for a new business card design with photo included.
Our business is a nonprofit construction contractor membership organization. We offer business education, assist with business setup and licensing, provide safety training, and provide a member directory.
URL: www.builderslinkguild.org
Color code:
CMYK: 0 cyan, 42 magenta, 100 yellow, 0 black for Print.
Hexidecimal: #FF9900
RGB: R 255; G 153; B 0

```html
<!DOCTYPE html>
<html lang="en">
<head>
<meta charset="utf-8">
<title>Northfield Builders Guild – Business Card</title>
<link href="https://fonts.googleapis.com/css2?family=Open+Sans:wght@400;800&family=Michroma&display=swap" rel="stylesheet">
<style>
  :root {
    --orange: #ff9900;
    --orange-deep: #f7991f;
    --charcoal: #333233;
    --ink: #3a3a3a;
    --white: #ffffff;
    --backdrop: #3b3b3b;
  }
  * { box-sizing: border-box; margin: 0; padding: 0; }
  html, body {
    width: 1200px; height: 780px; overflow: hidden;
    background: var(--backdrop);
  }
  .canvas {
    position: relative; width: 1200px; height: 780px;
  }
  .card {
    position: absolute; left: 75px; top: 90px;
    width: 1050px; height: 600px;
    border-radius: 32px; overflow: hidden;
    background: var(--white);
    font-family: "Open Sans", sans-serif;
    color: var(--ink);
  }
  .card-shapes { position: absolute; inset: 0; }
  .brand {
    position: absolute; left: 62px; top: 128px;
    display: flex; align-items: center; gap: 16px;
  }
  .brand-mark {
    width: 22px; height: 22px; background: var(--orange);
  }
  .brand-name {
    font-weight: 800; font-size: 40px; line-height: 1.05;
    color: var(--charcoal); letter-spacing: -0.5px;
  }
  .address {
    position: absolute; left: 66px; top: 292px;
    font-size: 21px; line-height: 1.45;
  }
  .contacts {
    position: absolute; left: 66px; top: 410px;
    list-style: none;
  }
  .contacts li {
    display: flex; align-items: center; gap: 22px;
    font-size: 21px; height: 44px;
  }
  .contacts svg { width: 30px; height: 30px; flex: none; }
  .person {
    position: absolute; left: 648px; top: 128px;
    white-space: nowrap;
  }
  .person-name {
    font-family: "Michroma", sans-serif;
    font-size: 20px; letter-spacing: 4px;
    color: var(--orange-deep);
  }
  .person-title {
    font-size: 17px; margin-top: 2px; color: var(--ink);
  }
</style>
</head>
<body>
<div class="canvas">
  <div class="card">
    <svg class="card-shapes" viewBox="0 0 1050 600" preserveAspectRatio="none" aria-hidden="true">
      <path class="band-orange" fill="var(--orange-deep)"
            d="M820,0 C960,80 1030,260 1000,380 C985,470 930,540 865,600 H1050 V0 Z"/>
      <path class="swoosh-dark" fill="var(--charcoal)"
            d="M945,175 C985,340 910,500 815,600 H560 C740,530 930,400 945,175 Z"/>
    </svg>

    <div class="brand">
      <span class="brand-mark"></span>
      <span class="brand-name">Northfield<br>Builders Guild</span>
    </div>

    <p class="address">118 Larkspur Avenue NW<br>Suite 210, Alder Falls MI 49021</p>

    <ul class="contacts">
      <li>
        <svg viewBox="0 0 24 24" fill="var(--orange)"><path d="M6.6 10.8a15 15 0 0 0 6.6 6.6l2.2-2.2a1 1 0 0 1 1-.25 11.4 11.4 0 0 0 3.6.57 1 1 0 0 1 1 1V20a1 1 0 0 1-1 1A17 17 0 0 1 3 4a1 1 0 0 1 1-1h3.5a1 1 0 0 1 1 1c0 1.25.2 2.45.57 3.57a1 1 0 0 1-.25 1z"/></svg>
        555-014-3920
      </li>
      <li>
        <svg viewBox="0 0 24 24" fill="var(--orange)"><path d="M7 3h10v4H7zM4 8h16a2 2 0 0 1 2 2v6h-4v5H6v-5H2v-6a2 2 0 0 1 2-2zm4 8v3h8v-3z"/></svg>
        555-014-3920
      </li>
      <li>
        <svg viewBox="0 0 24 24" fill="var(--orange)"><path d="M3 5h18v14H3zm2 2v.5l7 5 7-5V7zm0 3v7h14v-7l-7 5z"/></svg>
        danielreyes@northfieldmail.org
      </li>
      <li>
        <svg viewBox="0 0 24 24" fill="none" stroke="var(--orange)" stroke-width="1.6"><circle cx="12" cy="12" r="9"/><ellipse cx="12" cy="12" rx="4" ry="9"/><path d="M3 12h18M5 7h14M5 17h14"/></svg>
        www.builderslinkguild.org
      </li>
    </ul>

    <div class="person">
      <p class="person-name">DANIEL REYES</p>
      <p class="person-title">CEO/Managing Director</p>
    </div>
  </div>
</div>
</body>
</html>
```